Company web site

Looking for a full responsive(mobile friendly) wordpress implementation

Some material is in the website -- brelvanto.wordpress.com

But looking for a template more consistent with the logo design, and more future looking.

Target Market(s)

Enterprise Clients

Industry/Entity Type

It Company

Font styles to use
Sans Serif

Colors
33a6d7
0255a3
0455a3
cfdeed
85abd2
3176b5

Requirements
Must have
• about, contact information, partner page, success stories, customer testimonials. links to social presence.
• pricing information

```html
<!DOCTYPE html>
<html lang="en">
<head>
<meta charset="utf-8">
<title>Brelvanto — About</title>
<link rel="stylesheet" href="https://fonts.googleapis.com/css2?family=Jost:wght@400;500;600&display=swap">
<style>
  :root {
    --ink: #0e1114;
    --header-dark: #1f242b;
    --header-deep: #0d1013;
    --sky: #9cc0e4;
    --sky-soft: #b6d9ef;
    --panel: #d4e5f3;
    --panel-light: #dfeaf5;
    --brand-blue: #33a6d7;
    --tab-text: #3cc3ef;
    --tab-ink: #0b0d10;
    --tab-edge: #6a7f94;
    --link-grey: #e4e8ec;
    --deep-blue: #0255a3;
    --mid-blue: #3176b5;
    --footer-link: #2f9fd8;
  }
  * { box-sizing: border-box; margin: 0; padding: 0; }
  html, body { width: 1200px; height: 1056px; overflow: hidden; }
  body {
    position: relative;
    background: var(--sky);
    font-family: "Jost", "Century Gothic", sans-serif;
    color: var(--ink);
  }

  .site-header { position: absolute; left: 0; top: 0; width: 1200px; height: 318px; }
  .header-shapes { position: absolute; inset: 0; }

  .utility-nav {
    position: absolute; top: 4px; right: 32px;
    display: flex; list-style: none;
  }
  .utility-nav li {
    font-size: 20px; letter-spacing: 0.5px; color: var(--link-grey);
    padding: 0 20px; line-height: 30px;
    border-left: 2px solid var(--link-grey);
  }
  .utility-nav li:first-child { border-left: none; }
  .utility-nav li:last-child { padding-right: 0; }

  .brand {
    position: absolute; left: 232px; top: 92px;
    display: flex; align-items: center; gap: 34px;
  }
  .brand-mark {
    width: 120px; height: 120px; border-radius: 50%;
    background: var(--brand-blue);
  }
  .brand-name {
    font-size: 122px; font-weight: 500; color: var(--brand-blue);
    letter-spacing: 2px; line-height: 1;
  }

  .main-nav { position: absolute; left: 0; top: 318px; width: 1200px; height: 68px; }
  .main-nav svg { position: absolute; inset: 0; }
  .main-nav ul { list-style: none; }
  .main-nav li {
    position: absolute; top: 14px;
    font-size: 27px; font-weight: 600; color: var(--tab-text);
    letter-spacing: 0.5px; line-height: 1;
  }

  .content { position: absolute; left: 0; top: 386px; width: 1200px; height: 570px; }
  .content-shapes { position: absolute; inset: 0; }

  .about-title {
    position: absolute; left: 34px; top: 84px;
    font-size: 90px; font-weight: 400; line-height: 1; letter-spacing: 1px;
  }
  .about-copy {
    position: absolute; left: 34px; top: 178px; width: 720px;
    font-size: 18.5px; line-height: 22px;
  }
  .about-copy p + p { margin-top: 22px; }

  .world-network { position: absolute; left: 852px; top: 12px; width: 348px; height: 520px; }

  .site-footer {
    position: absolute; left: 0; top: 956px; width: 1200px; height: 100px;
    background: var(--header-dark);
  }
  .social-links {
    position: absolute; right: 60px; top: 22px;
    display: flex; gap: 18px; list-style: none;
  }
  .social-links li {
    display: flex; align-items: center; gap: 6px;
    font-size: 14px; font-weight: 500; color: var(--link-grey);
  }
  .social-links li::before {
    content: ""; width: 14px; height: 14px; background: var(--link-grey);
  }
  .footer-credit {
    position: absolute; right: 62px; bottom: 10px;
    font-size: 13px; color: var(--footer-link); letter-spacing: 0.3px;
  }
</style>
</head>
<body>

<header class="site-header">
  <svg class="header-shapes" width="1200" height="318" viewBox="0 0 1200 318" aria-hidden="true">
    <rect width="1200" height="318" fill="var(--header-dark)"/>
    <polygon points="0,0 160,0 510,110 1200,0 1200,255 510,258 0,300" fill="var(--header-deep)"/>
    <polygon points="510,110 1200,0 1200,255 510,258" fill="#0c0f12"/>
  </svg>
  <ul class="utility-nav">
    <li>LOGIN</li>
    <li>SUPPORT</li>
    <li>CONTACT</li>
    <li>PRIVACY POLICY</li>
  </ul>
  <div class="brand">
    <span class="brand-mark"></span>
    <span class="brand-name">Brelvanto</span>
  </div>
</header>

<nav class="main-nav">
  <svg width="1200" height="68" viewBox="0 0 1200 68" aria-hidden="true">
    <rect width="1200" height="68" fill="var(--sky)"/>
    <polygon points="22,12 180,12 172,50 26,50" fill="var(--tab-ink)"/>
    <polygon points="180,12 365,12 376,50 174,50" fill="var(--tab-ink)"/>
    <polygon points="368,12 578,12 574,50 380,50" fill="var(--tab-ink)"/>
    <polygon points="582,12 776,12 766,50 578,50" fill="var(--tab-ink)"/>
    <polygon points="766,52 976,52 968,60 772,60" fill="var(--tab-edge)"/>
    <polygon points="782,8 976,8 964,52 768,52" fill="var(--tab-ink)"/>
    <polygon points="980,12 1165,12 1160,50 968,50" fill="var(--tab-ink)"/>
  </svg>
  <ul>
    <li style="left:50px">HOME</li>
    <li style="left:215px">PLATFORM</li>
    <li style="left:414px">PARTNERS</li>
    <li style="left:632px">BLOG</li>
    <li style="left:836px;top:10px">ABOUT</li>
    <li style="left:1004px">CONTACT</li>
  </ul>
</nav>

<main class="content">
  <svg class="content-shapes" width="1200" height="570" viewBox="0 0 1200 570" aria-hidden="true">
    <rect width="1200" height="570" fill="var(--sky)"/>
    <polygon points="740,570 1200,290 1200,570" fill="var(--sky-soft)" opacity="0.6"/>
    <polygon points="0,0 812,44 812,494 0,524" fill="var(--panel)"/>
    <polygon points="0,166 772,166 772,362 0,424" fill="var(--panel-light)"/>
  </svg>

  <h1 class="about-title">ABOUT</h1>
  <div class="about-copy">
    <p>Founded in 2016 by industry veterans, Brelvanto is geared to provide integrated solutions for the IoT industry</p>
    <p>With a off-shore development center in Eastern Europe, Brelvanto is positioned to provided extensive development capabilities to our customers.</p>
  </div>

  <svg class="world-network" viewBox="0 0 348 520" role="img" aria-label="Glowing world map with network connection lines linking cities across continents">
    <defs>
      <radialGradient id="networkGlow" cx="0.55" cy="0.5" r="0.6">
        <stop offset="0" stop-color="#3a8fe0"/>
        <stop offset="0.5" stop-color="var(--deep-blue)"/>
        <stop offset="1" stop-color="#0a0f2a"/>
      </radialGradient>
    </defs>
    <polygon points="4,100 348,12 348,520 6,464" fill="url(#networkGlow)"/>
  </svg>
</main>

<footer class="site-footer">
  <ul class="social-links">
    <li>Codeshelf</li>
    <li>Workreach</li>
    <li>Circlebook</li>
    <li>Chirpline</li>
  </ul>
  <p class="footer-credit">PAGEWELL.COM.</p>
</footer>

</body>
</html>
```